The Brandwell Firm

We need a new design for our letterhead and envelopes. We are a personal injury and criminal defense firm so we need something modern and clean, but more on the professional/traditional side. Our new logo has two colors and is attached to the file so we need something that works well with those colors/matches the design. The following information needs to be on the letterhead:
Phone: (555) 214-3370
Fax: (555) 214-5186
Toll-Free: (888) 431-2059
Post Office Box 4721
Millbrook, SC 29555-4721
HarmClaimCounsel.example
PalmettoTrialAdvocates.example

Target Market(s)

Clients, government agencies, other law firms

Industry/Entity Type

Legal

Font styles to use
Sans Serif
Other font styles liked:
• Arial

Colors

Designer to choose colors to be used in the design.

Requirements
Must have
• Must look professional and clean, modern
Nice to have
• I would like to see a design that works with the logo but does not distract from the content that will be printed on it
Should not have
• Too many colors or crazy designs.

```html
<!DOCTYPE html>
<html lang="en">
<head>
<meta charset="utf-8">
<title>The Brandwell Firm — Letterhead &amp; Envelopes</title>
<link href="https://fonts.googleapis.com/css2?family=Lato:wght@400;700&display=swap" rel="stylesheet">
<style>
  :root {
    --navy: #2b2d87;
    --red: #c8202a;
    --paper: #efefef;
    --ink: #6e6e6e;
    --ink-dark: #4a4a4a;
    --backdrop: #d4d4d4;
  }
  * { margin: 0; padding: 0; box-sizing: border-box; }
  html, body { width: 1200px; height: 810px; overflow: hidden; }
  body {
    background: var(--backdrop);
    font-family: "Lato", Arial, sans-serif;
    color: var(--ink);
    position: relative;
  }
  .sheet { position: absolute; background: var(--paper); overflow: hidden; }

  /* brand name */
  .brand { display: flex; align-items: center; gap: 8px; }
  .brand-dot { width: 14px; height: 14px; border-radius: 50%; background: var(--red); flex: none; }
  .brand-name { font-weight: 700; font-size: 19px; color: var(--navy); letter-spacing: .2px; white-space: nowrap; }

  /* letterhead */
  .letterhead { left: 137px; top: 110px; width: 436px; height: 614px; }
  .letterhead .brand { position: absolute; left: 37px; top: 64px; }
  .contact { position: absolute; left: 307px; top: 56px; font-size: 7.4px; line-height: 9.2px; color: var(--ink-dark); }
  .contact-lines { margin-top: 6px; }
  .contact-row { display: flex; }
  .contact-label { color: var(--navy); width: 32px; }
  .contact-sep { width: 7px; }
  .recipient { position: absolute; left: 37px; top: 201px; font-size: 7.6px; line-height: 11.4px; }
  .body-copy { position: absolute; left: 37px; width: 362px; font-size: 7.4px; line-height: 11.4px; text-align: justify; }
  .body-copy.first { top: 269px; }
  .body-copy.second { top: 375px; }
  .signature { position: absolute; left: 36px; top: 436px; width: 86px; height: 56px; background: linear-gradient(135deg, rgba(43,45,135,.18), rgba(43,45,135,.06)); border-radius: 4px; }
  .sign-title { position: absolute; left: 36px; top: 500px; font-size: 7.4px; }

  .footer-band { position: absolute; left: 0; bottom: 0; width: 100%; }
  .footer-band svg { display: block; }
  .footer-links { position: absolute; left: 30px; top: 0; height: 100%; display: flex; align-items: center; font-size: 7.4px; color: #fff; }
  .footer-links .divider { margin: 0 6px; }

  /* envelope back */
  .envelope-back { left: 619px; top: 194px; width: 444px; height: 221px; }
  .envelope-back .flap { position: absolute; left: 0; top: 0; }
  .flap-mark { position: absolute; left: 214px; top: 24px; width: 16px; height: 16px; border-radius: 50%; background: #fff; }

  /* envelope front */
  .envelope-front { left: 618px; top: 444px; width: 445px; height: 220px; }
  .envelope-front .brand { position: absolute; left: 24px; top: 48px; }
  .return-address { position: absolute; left: 25px; top: 105px; font-size: 7.4px; line-height: 9.6px; color: var(--ink-dark); }
  .envelope-front .footer-links { left: 26px; }
</style>
</head>
<body>

<section class="sheet letterhead">
  <div class="brand">
    <span class="brand-dot"></span>
    <span class="brand-name">The Brandwell Firm</span>
  </div>

  <div class="contact">
    <div>Post Office Box 4721</div>
    <div>Millbrook, SC 29555-4721</div>
    <div class="contact-lines">
      <div class="contact-row"><span class="contact-label">Phone</span><span class="contact-sep">:</span><span>(555) 214-3370</span></div>
      <div class="contact-row"><span class="contact-label">Fax</span><span class="contact-sep">:</span><span>(555) 214-5186</span></div>
      <div class="contact-row"><span class="contact-label">Toll-Free</span><span class="contact-sep">:</span><span>(888) 431-2059</span></div>
    </div>
  </div>

  <div class="recipient">
    <div>Dear Hallorin</div>
    <div>Northgate Print Works</div>
    <div>Department Design</div>
  </div>

  <p class="body-copy first">Lorem ipsum dolor sit amet, consectetuer adipiscing elit. Aenean commodo ligula eget dolor. Aenean massa. Cum sociis natoque penatibus et magnis dis parturient montes, nascetur ridiculus mus. Donec quam felis, ultricies nec, pellentesque eu, pretium quis, sem. Nulla consequat massa quis enim. Donec pede justo, fringilla vel, aliquet nec, vulputate eget, arcu. In enim justo, rhoncus ut, imperdiet a, venenatis vitae, justo. Nullam dictum felis eu pede mollis pretium. Integer tincidunt. Cras dapibus. Vivamus elementum semper nisi.Nullam dictum felis eu pede mollis pretium. Integer tincidunt. Cras dapibus. Vivamus elementum semper nisi.felis eu pede mollis pretium. Integer tincidunt. Cras dapibus.</p>

  <p class="body-copy second">Quisque rutrum. Aenean imperdiet. Etiam ultricies nisi vel augue. Curabitur ullamcorper ultricies nisi. Nam eget dui. Etiam rhoncus. Maecenas tempus, tellus eget condimentum rhoncus, sem quam semper libero, sit amet adipiscing sem neque sed ipsum.felis pede mollis pretium. I am tincidunt. Cras dapibus.</p>

  <div class="signature" role="img" aria-label="Handwritten signature of the director"></div>
  <div class="sign-title">Director/Excecutive Director</div>

  <div class="footer-band">
    <svg width="436" height="18" viewBox="0 0 436 18" aria-hidden="true">
      <rect x="0" y="0" width="436" height="18" fill="var(--navy)"/>
      <path d="M282 18 Q296 6 326 6 L436 6 L436 18 Z" fill="#fff"/>
      <path d="M290 18 Q302 9 328 9 L436 9 L436 18 Z" fill="var(--red)"/>
    </svg>
    <div class="footer-links">
      <span>www.HarmClaimCounsel.example</span><span class="divider">|</span><span>www.PalmettoTrialAdvocates.example</span>
    </div>
  </div>
</section>

<section class="sheet envelope-back">
  <svg class="flap" width="444" height="66" viewBox="0 0 444 66" aria-hidden="true">
    <path d="M0 0 H444 L436 56 Q435 65 425 65 H19 Q9 65 8 56 Z" fill="var(--navy)"/>
  </svg>
  <span class="flap-mark"></span>
</section>

<section class="sheet envelope-front">
  <div class="brand">
    <span class="brand-dot"></span>
    <span class="brand-name">The Brandwell Firm</span>
  </div>
  <div class="return-address">
    <div>Post Office Box 4721</div>
    <div>Millbrook, SC 29555-4721</div>
  </div>
  <div class="footer-band">
    <svg width="445" height="17" viewBox="0 0 445 17" aria-hidden="true">
      <rect x="0" y="0" width="445" height="17" fill="var(--navy)"/>
      <path d="M298 17 Q312 6 342 6 L445 6 L445 17 Z" fill="#fff"/>
      <path d="M306 17 Q318 9 344 9 L445 9 L445 17 Z" fill="var(--red)"/>
    </svg>
    <div class="footer-links">
      <span>www.HarmClaimCounsel.example</span><span class="divider">|</span><span>www.PalmettoTrialAdvocates.example</span>
    </div>
  </div>
</section>

</body>
</html>
```